REDESIGN MAIN BANNER IMAGE FOR MARKETING WEBSITE

I feel like my main banner image is too busy but I like it but i want to see other options. www.brightlanepromoworks.biz I want a nice professional clean design that goes with current theme of site. Must look professional and show the variety of incentives we offer but not be overwelming.

My business is called Brightlane Promo Works and I provide businesses around the world with marketing incentives that they can use to create exciting promotions and contest and marketing giveaways to help attract more customers.

I provide a variety of different types of incentives such as Vacation Certificates, Dining Vouchers, Hotel Savings Cards, Smart Watches, Etc. that businesses can use in their marketing efforts.

I want my main banner image to reflect the variety of different categories of incentives... that I offer here: https://www.brightlanepromoworks.biz/incentives

We can use images of certificates or images.....I just want the content to be the same:

CONTENT FOR MAIN BANNER IMAGE:
INCREASE LEADS AND SALES OVERNIGHT

CREATE EXCITING MARKETING PROMOTIONS GIVING AWAY SMART DEVICES, VACATION CERTIFICATES, DINING VOUCHERS AND OTHER INCENTIVES TO YOUR CUSTOMERS

GET A FREE SAMPLE PACKAGE FOR A LIMITED TIME ONLY

Target Market(s)

b2b business owners, ceo, president, owner, founder

Industry/Entity Type

Promotional

Requirements
Must have
• Hi guys keep in mind the finished product will have to be 1800x840

Nice to have
• I want a nice professional clean design that goes with current theme of site. Must look professional and show the variety of incentives we offer but not be overwelming.
Should not have

```html
<!DOCTYPE html>
<html lang="en">
<head>
<meta charset="utf-8">
<title>Brightlane Promo Works – Increase Leads &amp; Sales Overnight</title>
<link rel="stylesheet" href="https://fonts.googleapis.com/css2?family=Archivo+Black&family=Russo+One&family=Anton&family=Roboto:wght@400;700;900&display=swap">
<style>
  :root {
    --red: #d0121b;
    --red-dark: #a40c13;
    --blue: #0f59a8;
    --green: #1f9b3b;
    --green-light: #3cc155;
    --white: #ffffff;
    --ink: #1c1f26;
    --grey: #8a8f98;
    --tag-text: #ffe94a;
  }
  * { box-sizing: border-box; margin: 0; padding: 0; }
  html, body { width: 1200px; height: 560px; overflow: hidden; background: var(--white); }
  ul { list-style: none; }
  .banner { position: relative; width: 1200px; height: 560px; font-family: "Roboto", sans-serif; }

  .banner__shapes { position: absolute; inset: 0; }

  .headline {
    position: absolute; left: 24px; top: 0; width: 1152px; height: 103px;
    display: flex; align-items: center; justify-content: center;
    font-family: "Archivo Black", sans-serif; font-size: 49px; letter-spacing: -0.5px;
    color: var(--white); white-space: nowrap;
  }

  .ribbon {
    position: absolute; left: 52px; top: 120px; width: 138px;
    text-align: center; color: var(--white); font-family: "Russo One", sans-serif;
    font-size: 20px; line-height: 21px;
  }
  .ribbon__price { display: block; font-family: "Archivo Black", sans-serif; font-size: 21px; margin-top: 2px; }

  .tagline {
    position: absolute; left: 246px; top: 124px;
    font-family: "Russo One", sans-serif; font-size: 23px; color: var(--white); white-space: nowrap;
  }

  .categories { position: absolute; top: 172px; left: 0; width: 1000px; height: 50px; }
  .category { position: absolute; display: flex; align-items: center; gap: 14px; color: var(--white); }
  .category svg { flex: none; }
  .category__label { font-family: "Russo One", sans-serif; font-size: 17px; line-height: 17px; }

  .badge { position: absolute; left: 1012px; top: 90px; width: 180px; height: 180px; }
  .badge__text {
    position: absolute; left: 1030px; top: 128px; width: 140px; text-align: center;
    color: var(--white); transform: rotate(-3deg);
  }
  .badge__big { font-family: "Archivo Black", sans-serif; font-size: 30px; line-height: 30px; display: block; }
  .badge__small { font-family: "Archivo Black", sans-serif; font-size: 11px; line-height: 14px; display: block; margin-top: 3px; }

  .certificates { position: absolute; inset: 0; }
  .reflection {
    position: absolute; left: 42px; top: 508px; width: 1111px; height: 36px;
    background: linear-gradient(to bottom, rgba(200,200,205,.35), rgba(255,255,255,0));
  }
  .card {
    position: absolute; width: 122px; height: 240px; background: var(--white);
    box-shadow: 0 2px 6px rgba(0,0,0,.35); overflow: hidden;
    display: flex; flex-direction: column;
  }
  .card__head {
    position: relative; height: 30px; flex: none; background: var(--ink); padding: 0 5px;
    display: flex; align-items: center; gap: 4px;
  }
  .card__enjoy { font-family: "Anton", sans-serif; font-size: 17px; line-height: 20px; color: var(--white); }
  .card__tag {
    background: var(--red); color: var(--tag-text); white-space: nowrap;
    font-family: "Anton", sans-serif; font-size: 8px; line-height: 10px; padding: 1px 3px;
  }
  .card__photo { height: 78px; flex: none; }
  .card__band {
    background: var(--red); color: var(--white); font-size: 3.6px; font-weight: 700;
    padding: 2px 5px; text-transform: uppercase;
  }
  .card__copy { padding: 3px 5px 0; font-size: 3.4px; line-height: 4.4px; color: #555; }
  .card__heading { margin-top: 3px; background: var(--red-dark); color: var(--white); font-size: 3.6px; font-weight: 700; padding: 1px 5px; width: 60%; }
  .card__foot {
    margin-top: auto; display: flex; justify-content: space-between; padding: 4px 5px 6px;
    font-size: 3.8px; color: var(--ink); font-weight: 700; border-top: 1px solid #ddd;
  }
  .card__foot b { color: var(--red); }
  .card__compliments {
    position: absolute; right: 4px; top: 3px; width: 44px; height: 34px; background: var(--white);
    border: 1px solid #ccc; text-align: center; font-size: 3.6px; color: var(--grey); padding-top: 3px;
  }
  .card__compliments strong { display: block; font-size: 10px; color: #999; font-weight: 900; }
  .card__dots { position: absolute; right: 3px; top: 118px; display: flex; flex-direction: column; gap: 5px; }
  .card__dot { width: 26px; height: 26px; border-radius: 50%; border: 2px solid var(--white); box-shadow: 0 1px 2px rgba(0,0,0,.4); }

  .cta {
    position: absolute; z-index: 20; left: 455px; top: 483px; width: 290px; height: 50px;
    border-radius: 6px; background: linear-gradient(to bottom, var(--green-light), var(--green));
    box-shadow: 0 3px 6px rgba(0,0,0,.3);
    display: flex; align-items: center; justify-content: center;
    font-family: "Russo One", sans-serif; font-size: 19px; color: var(--white); text-decoration: none;
  }
</style>
</head>
<body>
<div class="banner">

  <svg class="banner__shapes" width="1200" height="560" viewBox="0 0 1200 560" aria-hidden="true">
    <path d="M24 103 H1176 V208 Q1176 224 1160 224 L760 224 C690 240 630 266 600 270 C570 266 510 240 440 224 L42 224 Q24 224 24 206 Z" fill="var(--blue)"/>
    <rect x="24" y="0" width="1152" height="103" fill="var(--red)"/>
    <polygon points="52,103 190,103 190,257 121,232 52,257" fill="var(--red)"/>
    <polygon points="57,108 185,108 185,250 121,227 57,250" fill="none" stroke="var(--white)" stroke-width="1" stroke-dasharray="4 3"/>
  </svg>

  <h1 class="headline">INCREASE LEADS &amp; SALES OVERNIGHT</h1>

  <p class="ribbon">Unlimited Incentives Only <span class="ribbon__price">$99/mth</span></p>

  <p class="tagline">Attract new customers with high value marketing incentives:</p>

  <ul class="categories">
    <li class="category" style="left:241px;top:3px">
      <svg width="68" height="44" viewBox="0 0 68 44" fill="var(--white)">
        <rect x="14" y="0" width="26" height="36" rx="3"/>
        <rect x="18" y="4" width="18" height="26" fill="var(--blue)"/>
        <rect x="36" y="12" width="30" height="22" rx="2"/>
        <rect x="39" y="15" width="24" height="16" fill="var(--blue)"/>
        <rect x="30" y="34" width="38" height="4" rx="1"/>
        <rect x="0" y="20" width="10" height="22" rx="2"/>
        <rect x="4" y="12" width="3" height="8"/>
      </svg>
      <span class="category__label">Smart<br>Devices</span>
    </li>
    <li class="category" style="left:434px;top:3px">
      <svg width="74" height="38" viewBox="0 0 74 38">
        <path d="M0 4 Q0 0 4 0 H70 Q74 0 74 4 V14 Q68 19 74 24 V34 Q74 38 70 38 H4 Q0 38 0 34 V24 Q6 19 0 14 Z" fill="var(--white)"/>
        <circle cx="28" cy="12" r="5" fill="var(--blue)"/>
        <circle cx="46" cy="26" r="5" fill="var(--blue)"/>
        <line x1="48" y1="8" x2="26" y2="30" stroke="var(--blue)" stroke-width="4" stroke-linecap="round"/>
      </svg>
      <span class="category__label">Dining<br>Vochers</span>
    </li>
    <li class="category" style="left:614px;top:0">
      <svg width="72" height="46" viewBox="0 0 72 46" fill="var(--white)">
        <rect x="0" y="0" width="64" height="34" rx="2"/>
        <rect x="6" y="6" width="52" height="3" fill="var(--blue)"/>
        <rect x="6" y="13" width="40" height="3" fill="var(--blue)"/>
        <rect x="6" y="20" width="34" height="3" fill="var(--blue)"/>
        <circle cx="56" cy="30" r="8" stroke="var(--blue)" stroke-width="2"/>
        <polygon points="51,36 51,46 56,42 61,46 61,36"/>
      </svg>
      <span class="category__label">Vacation<br>Certificates</span>
    </li>
    <li class="category" style="left:820px;top:0">
      <svg width="44" height="44" viewBox="0 0 44 44" fill="var(--white)">
        <rect x="0" y="10" width="44" height="10"/>
        <rect x="3" y="22" width="38" height="22"/>
        <rect x="19" y="10" width="6" height="34" fill="var(--blue)"/>
        <path d="M22 10 C14 -2 4 4 12 10 Z M22 10 C30 -2 40 4 32 10 Z"/>
      </svg>
      <span class="category__label">Other<br>Incentives</span>
    </li>
  </ul>

  <svg class="badge" viewBox="0 0 180 180" aria-hidden="true">
    <defs>
      <radialGradient id="badgeFill" cx="50%" cy="40%" r="60%">
        <stop offset="0" stop-color="#2fb04a"/>
        <stop offset="1" stop-color="#15802e"/>
      </radialGradient>
    </defs>
    <circle cx="90" cy="88" r="80" fill="url(#badgeFill)"/>
    <path d="M18 56 Q30 18 66 8 L60 58 Z" fill="var(--white)"/>
    <path d="M18 56 L60 58 L66 8 Q44 26 18 56 Z" fill="#e6e6e6"/>
  </svg>
  <p class="badge__text">
    <span class="badge__big">GET<br>A FREE</span>
    <span class="badge__small">SAMPLE PACKAGE<br>FOR A LIMITED<br>TIME ONLY</span>
  </p>

  <div class="certificates">
    <div class="reflection"></div>

    <article class="card" style="left:1050px;top:267px;width:103px;z-index:1">
      <div class="card__head"><span class="card__enjoy">ENJOY</span><span class="card__compliments">Compliments Of<strong>LOGO</strong></span></div>
      <div class="card__photo" role="img" aria-label="Photo of wine bottles and grapes" style="background:linear-gradient(135deg,#5a1a2a,#a63244)"></div>
      <div class="card__band">Exclusively for: customer name</div>
      <p class="card__copy">Redeem this certificate online for your exclusive reward.</p>
      <div class="card__foot"><span>Certificate ID</span><b>prizepathrewards.com</b></div>
    </article>
    <article class="card" style="left:965px;top:272px;z-index:2">
      <div class="card__head"><span class="card__enjoy">ENJOY</span><span class="card__compliments">Compliments Of<strong>LOGO</strong></span></div>
      <div class="card__photo" role="img" aria-label="Photo of a beach getaway" style="background:linear-gradient(135deg,#f0d9b0,#c9a06c)"></div>
      <div class="card__band">Exclusively for: customer name</div>
      <p class="card__copy">Redeem this certificate online for your exclusive reward.</p>
      <div class="card__dots"><span class="card__dot" role="img" aria-label="Photo of a gift" style="background:#c8282e"></span><span class="card__dot" role="img" aria-label="Photo of a pool" style="background:#3aa6c9"></span></div>
      <div class="card__foot"><span>Certificate ID</span><b>prizepathrewards.com</b></div>
    </article>
    <article class="card" style="left:880px;top:277px;z-index:3">
      <div class="card__head"><span class="card__enjoy">ENJOY</span><span class="card__compliments">Compliments Of<strong>LOGO</strong></span></div>
      <div class="card__photo" role="img" aria-label="Photo of an airliner in flight" style="background:linear-gradient(135deg,#d9e6f2,#8fb0cf)"></div>
      <div class="card__band">Exclusively for: customer name</div>
      <p class="card__copy">Redeem this certificate online for your exclusive reward.</p>
      <div class="card__dots"><span class="card__dot" role="img" aria-label="Photo of a resort" style="background:#8a6a4a"></span><span class="card__dot" role="img" aria-label="Photo of a city" style="background:#6d7f92"></span></div>
      <div class="card__foot"><span>Certificate ID</span><b>prizepathrewards.com</b></div>
    </article>
    <article class="card" style="left:795px;top:290px;z-index:4">
      <div class="card__head"><span class="card__enjoy">ENJOY</span><span class="card__tag">AIRFARE</span></div>
      <div class="card__photo" role="img" aria-label="Photo of a travel destination" style="background:linear-gradient(135deg,#2e5e8e,#a3c3df)"></div>
      <div class="card__band">Exclusively for: customer name</div>
      <p class="card__copy">Redeem this certificate online for your exclusive reward.</p>
      <div class="card__dots"><span class="card__dot" role="img" aria-label="Photo of a meal" style="background:#8c4a2a"></span><span class="card__dot" role="img" aria-label="Photo of a dinner table" style="background:#b77a45"></span><span class="card__dot" role="img" aria-label="Photo of a dessert" style="background:#6e3a22"></span></div>
      <div class="card__foot"><span>Certificate ID</span><b>prizepathrewards.com</b></div>
    </article>
    <article class="card" style="left:715px;top:305px;z-index:5">
      <div class="card__head"><span class="card__enjoy">ENJOY</span><span class="card__compliments">Compliments Of<strong>LOGO</strong></span></div>
      <div class="card__photo" role="img" aria-label="Photo of a restaurant dinner" style="background:linear-gradient(135deg,#3a1e14,#9a5a32)"></div>
      <div class="card__band">Exclusively for: customer name</div>
      <p class="card__copy">Redeem this certificate online for your exclusive reward.</p>
      <div class="card__dots"><span class="card__dot" role="img" aria-label="Photo of a plated dish" style="background:#a4542c"></span><span class="card__dot" role="img" aria-label="Photo of a salad" style="background:#5e7a34"></span><span class="card__dot" role="img" aria-label="Photo of pasta" style="background:#c58a44"></span></div>
      <div class="card__foot"><span>Certificate ID</span><b>prizepathrewards.com</b></div>
    </article>
    <article class="card" style="left:640px;top:312px;z-index:6">
      <div class="card__head"><span class="card__enjoy">ENJOY</span><span class="card__tag">$200 OFF</span></div>
      <div class="card__photo" role="img" aria-label="Photo of diners in a restaurant" style="background:linear-gradient(135deg,#4a2418,#b0663a)"></div>
      <div class="card__band">Exclusively for: customer name</div>
      <p class="card__copy">Redeem this certificate online for your exclusive reward.</p>
      <div class="card__foot"><span>Certificate ID</span><b>prizepathrewards.com</b></div>
    </article>

    <article class="card" style="left:42px;top:267px;z-index:1">
      <div class="card__head"><span class="card__enjoy">ENJOY</span><span class="card__tag">STERILIZER</span></div>
      <div class="card__photo" role="img" aria-label="Photo of a UV smartphone sterilizer" style="background:linear-gradient(135deg,#0f3a66,#5fa8d6)"></div>
      <div class="card__band">Exclusively for: customer name</div>
      <p class="card__copy">Redeem this certificate online for your exclusive reward.</p>
      <div class="card__heading">FEATURES</div>
      <div class="card__foot"><span>Certificate ID</span><b>VIEW ALL</b></div>
    </article>
    <article class="card" style="left:138px;top:272px;z-index:2">
      <div class="card__head"><span class="card__enjoy">ENJOY</span><span class="card__tag">MP4 PLAYER</span></div>
      <div class="card__photo" role="img" aria-label="Photo of colourful MP4 players" style="background:linear-gradient(135deg,#5a3aa0,#d04a7a)"></div>
      <div class="card__band">Exclusively for: customer name</div>
      <p class="card__copy">Redeem this certificate online for your exclusive reward.</p>
      <div class="card__heading">FEATURES</div>
      <div class="card__foot"><span>Certificate ID</span><b>VIEW ALL</b></div>
    </article>
    <article class="card" style="left:230px;top:279px;z-index:3">
      <div class="card__head"><span class="card__enjoy">ENJOY</span><span class="card__tag">HD TABLET</span></div>
      <div class="card__photo" role="img" aria-label="Photo of an HD tablet" style="background:linear-gradient(135deg,#1e2a22,#5f8f3a)"></div>
      <div class="card__band">Exclusively for: customer name</div>
      <p class="card__copy">Redeem this certificate online for your exclusive reward.</p>
      <div class="card__heading">FEATURES</div>
      <div class="card__foot"><span>Certificate ID</span><b>VIEW ALL</b></div>
    </article>
    <article class="card" style="left:320px;top:303px;z-index:4">
      <div class="card__head"><span class="card__enjoy">ENJOY</span><span class="card__tag">HOTEL STAY</span></div>
      <div class="card__photo" role="img" aria-label="Photo of a hotel lobby" style="background:linear-gradient(135deg,#4a3524,#b08a5a)"></div>
      <div class="card__band">Exclusively for: customer name</div>
      <p class="card__copy">Redeem this certificate online for your exclusive reward.</p>
      <div class="card__heading">FEATURES</div>
      <div class="card__foot"><span>Certificate ID</span><b>VIEW ALL</b></div>
    </article>
    <article class="card" style="left:420px;top:309px;z-index:5">
      <div class="card__head"><span class="card__enjoy">ENJOY</span><span class="card__tag">HOTEL STAY</span></div>
      <div class="card__photo" role="img" aria-label="Photo of a hotel pool" style="background:linear-gradient(135deg,#3c2c20,#a37a4c)"></div>
      <div class="card__band">Exclusively for: customer name</div>
      <p class="card__copy">Redeem this certificate online for your exclusive reward.</p>
      <div class="card__heading">FEATURES</div>
      <div class="card__foot"><span>Certificate ID</span><b>VIEW ALL</b></div>
    </article>

    <article class="card" style="left:528px;top:314px;width:142px;height:232px;z-index:7">
      <div class="card__head"><span class="card__enjoy">ENJOY</span><span class="card__tag">4 NIGHTS</span></div>
      <div class="card__photo" role="img" aria-label="Illustration of a Las Vegas getaway" style="height:88px;background:linear-gradient(135deg,#f4c23a,#d0121b)"></div>
      <div class="card__band">Exclusively for: customer name</div>
      <p class="card__copy">Redeem this certificate online for your exclusive reward.</p>
      <div class="card__heading">FEATURES</div>
      <div class="card__dots" style="top:92px"><span class="card__dot" role="img" aria-label="Photo of a casino sign" style="background:#a0141a"></span><span class="card__dot" role="img" aria-label="Photo of a resort at night" style="background:#2a2f5a"></span></div>
      <div class="card__foot"><span>Certificate ID</span><b>VIEW ALL</b></div>
    </article>
  </div>

  <a class="cta" href="#">Get A Free Sample Package</a>
</div>
</body>
</html>
```